Upscale business cards needed for Board of Directors

We need professional business cards created for members of our family business Board of Directors. We would like these relatively simple and straightforward, but also with a unique element to set them apart. Probably stick with neutral and simple colors - white, grey etc. We need space for the traditional elements, including name, title, address, email/phone number. And we will be creating several from this template so it needs to be template that is easy to switch information in and out of.
Business
See description

```html
<!DOCTYPE html>
<html lang="en">
<head>
<meta charset="utf-8">
<title>Harborline Holdings – Business Card</title>
<link rel="stylesheet" href="https://fonts.googleapis.com/css2?family=Roboto:wght@400;500;700&display=swap">
<style>
  :root {
    --backdrop: #3a322e;
    --card: #161616;
    --card-edge: #222222;
    --white: #f2f2f2;
    --silver: #bdbdbd;
    --muted: #8d8d8d;
    --gold: #b89c6e;
  }
  * { box-sizing: border-box; margin: 0; padding: 0; }
  html, body { width: 1200px; height: 864px; overflow: hidden; }
  body {
    background: var(--backdrop);
    font-family: "Roboto", Arial, sans-serif;
    position: relative;
  }
  .card {
    position: absolute;
    top: 277px;
    width: 540px;
    height: 309px;
    background: var(--card);
    border: 1px solid var(--card-edge);
    box-shadow: 0 18px 40px rgba(0,0,0,.45);
  }
  .card--front { left: 40px; }
  .card--back { left: 620px; }

  .wordmark {
    font-weight: 700;
    text-transform: uppercase;
    line-height: 1;
  }
  .wordmark__main { display: block; font-size: 44px; letter-spacing: 1px; }
  .wordmark__sub { display: block; font-size: 21px; letter-spacing: 9px; margin-top: 4px; }

  .card--front .wordmark {
    position: absolute; left: 100px; top: 104px; color: var(--silver);
  }
  .card--front .wordmark__sub { padding-left: 30px; }
  .front-web {
    position: absolute; left: 100px; top: 218px;
    color: var(--muted); font-size: 13px; letter-spacing: 4px;
  }

  .card--back .wordmark {
    position: absolute; right: 34px; top: 64px; color: var(--white); text-align: right;
  }
  .card--back .wordmark__main { font-size: 40px; }
  .card--back .wordmark__sub { font-size: 19px; letter-spacing: 8px; }

  .person { position: absolute; left: 30px; top: 58px; }
  .person__name { color: var(--gold); font-size: 17px; font-weight: 500; }
  .person__title { color: var(--white); font-size: 14px; margin-top: 3px; }

  .contact { position: absolute; left: 30px; top: 116px; list-style: none; }
  .contact__item {
    display: flex; align-items: center; gap: 9px;
    color: var(--white); font-size: 12.5px; height: 19px;
  }
  .contact__icon { width: 12px; height: 12px; fill: var(--gold); flex: none; }

  .rule { position: absolute; height: 1px; background: var(--white); }
  .rule--main { left: 30px; right: 0; top: 186px; }
  .rule--address { left: 330px; right: 34px; top: 236px; }

  .address {
    position: absolute; left: 330px; top: 246px;
    color: var(--white); font-size: 13px; font-style: normal; line-height: 1.45;
  }
</style>
</head>
<body>
  <section class="card card--front" aria-label="Card front">
    <div class="wordmark">
      <span class="wordmark__main">Harborline</span>
      <span class="wordmark__sub">Holdings</span>
    </div>
    <p class="front-web">www.harborline.com</p>
  </section>

  <section class="card card--back" aria-label="Card back">
    <div class="person">
      <p class="person__name">Mark Ellis</p>
      <p class="person__title">President</p>
    </div>
    <ul class="contact">
      <li class="contact__item">
        <svg class="contact__icon" viewBox="0 0 24 24" aria-hidden="true"><path d="M6.6 10.8a15 15 0 0 0 6.6 6.6l2.2-2.2a1 1 0 0 1 1-.25 11.4 11.4 0 0 0 3.6.57 1 1 0 0 1 1 1V20a1 1 0 0 1-1 1A17 17 0 0 1 3 4a1 1 0 0 1 1-1h3.5a1 1 0 0 1 1 1c0 1.25.2 2.45.57 3.57a1 1 0 0 1-.25 1z"/></svg>
        <span>555 0142 7788</span>
      </li>
      <li class="contact__item">
        <svg class="contact__icon" viewBox="0 0 24 24" aria-hidden="true"><path d="M2 5h20v14H2z M3 6l9 7 9-7" fill="none" stroke="#b89c6e" stroke-width="2.4"/></svg>
        <span>mark@harborline.com</span>
      </li>
      <li class="contact__item">
        <svg class="contact__icon" viewBox="0 0 24 24" aria-hidden="true"><circle cx="12" cy="12" r="10" fill="none" stroke="#b89c6e" stroke-width="2.4"/><path d="M2 12h20M12 2c3 3 3 17 0 20M12 2c-3 3-3 17 0 20" fill="none" stroke="#b89c6e" stroke-width="2"/></svg>
        <span>www.harborline.com</span>
      </li>
    </ul>
    <div class="wordmark">
      <span class="wordmark__main">Harborline</span>
      <span class="wordmark__sub">Holdings</span>
    </div>
    <div class="rule rule--main"></div>
    <div class="rule rule--address"></div>
    <address class="address">2170 Linden Avenue<br>Maple Grove, NY 11020</address>
  </section>
</body>
</html>
```